Start-up braucht modernes/hochwertiges Getränkeetikett
Zielgruppe
Wir sind ein modernes, nachhaltiges Start-up, welches eine neue Getränkekategorie auf den Markt bringt. Ein sogenanntes Elektrolyt-Getränk mit dem Namen FLUXO4. Es ist abgefüllt in eine 500 ml Flasche und enthält Magnesium, Kalzium, Kalium, und Natrium. Diese Stoffe (Elektrolyte) dienen der körperlichen Hydrierung. Zu Dehydrierung kann es durch Hitze, Alkohol, Sport oder Krankheit kommen. Krankheit liegt bei uns allerdings nicht im Fokus. In unserer Zielgruppe befinden sich hauptsächlich Personen im Alter von 18 - 29 Jahren.
Die Geschmacksrichtung ist Zitrone-Limette.
Aufgabenstellung
Das Etikett soll:
- MODERN, SCHLICHT und HOCHWERTIG sein, so dass es im Supermarkt hervorsticht
- erkenntlich machen, dass die Stoffe Magnesium, Natrium, Kalzium und Kalium enthalten sind
- sich farblich deutlich von der Farbe des Inhalts (weiß) abheben. (Vorzugsweise mit einem hellen Blau, türkis)
- für unsere junge Zielgruppe ansprechend sein
- ebenfalls auf die Geschmacksrichtung (Zitrone-Limette) hinweisen, und zwar so, dass wenn man eine weitere Geschmacksrichtung auf den Markt bringen möchte, diese leicht angepasst werden kann.
- nicht nach einem Energydrink oder einem typischen Sportgetränk aussehen
- unter dem Namen den Slogan 'Elektrolyt-Getränk' stehen haben
-Das Etikett ist nicht dursichtig sondern besteht aus Papier
Der Name sowie das Logo können selbstverständlich farblich verändert werden. Bei dem Logo können auch größere Änderungen vollzogen werden.
Bitte beachten Sie die unten zu stehenden Regler um sich einen guten Überblick über unsere Vorstellungen zu verschaffen. Die Platzierung des EAN-Code ist für ihr Design irrelevat .
Bei Unklarheiten gerne nachfragen!

```html
<!DOCTYPE html>
<html lang="de">
<head>
<meta charset="utf-8">
<title>FLUXO4 – Elektrolyt-Getränk Etikett</title>
<link rel="stylesheet" href="https://fonts.googleapis.com/css2?family=Comfortaa:wght@400;700&display=swap">
<style>
  :root {
    --stage: #e4e6e8;
    --paper: #ffffff;
    --teal-light: #9fd9cf;
    --teal-mid: #5fb3a8;
    --teal-deep: #2f7c76;
    --slate-edge: #8a9ba3;
    --slate-core: #13262f;
    --bar: #23343c;
    --ink-light: #eef3f4;
    --ink-slogan: #5d7380;
    --lemon: #e8e24a;
    --lime: #a9d36e;
  }
  * { box-sizing: border-box; margin: 0; padding: 0; }
  html, body {
    width: 667px; height: 1200px; overflow: hidden;
    background: var(--stage);
    font-family: "Comfortaa", sans-serif;
  }
  .label {
    position: absolute; left: 0; top: 85px;
    width: 667px; height: 1029px;
    background: var(--paper);
    display: flex; flex-direction: column;
  }
  .mineral-band {
    position: relative; height: 270px;
  }
  .mineral-texture {
    position: absolute; inset: 0;
    background:
      radial-gradient(ellipse at 30% 40%, var(--teal-light) 0%, transparent 60%),
      radial-gradient(ellipse at 55% 60%, var(--teal-deep) 0%, transparent 45%),
      linear-gradient(135deg, var(--teal-light), var(--teal-mid) 55%, var(--teal-light));
  }
  .element-list { position: absolute; left: 285px; right: 0; top: 0; list-style: none; }
  .element {
    position: absolute; left: 0; right: 0; height: 38px;
    background: var(--bar);
    color: var(--ink-light);
    display: flex; align-items: center;
  }
  .element:nth-child(1) { top: 39px; }
  .element:nth-child(2) { top: 97px; }
  .element:nth-child(3) { top: 156px; }
  .element:nth-child(4) { top: 214px; }
  .element-symbol {
    width: 84px; text-align: center;
    font-weight: 700; font-size: 18px; letter-spacing: 1px;
  }
  .element-name { font-size: 19px; letter-spacing: 1px; text-transform: lowercase; }

  .brand-band {
    position: relative; height: 405px;
    background: linear-gradient(90deg, var(--slate-edge) 0%, var(--slate-core) 45%, var(--slate-core) 60%, var(--slate-edge) 100%);
    color: var(--ink-light);
    text-align: center;
  }
  .brand-mark {
    position: absolute; left: 50%; top: 39px;
    width: 226px; height: 226px; margin-left: -113px;
    border: 2px solid var(--ink-light); border-radius: 50%;
  }
  .brand-name {
    position: absolute; left: 0; right: 0; top: 290px;
    font-size: 56px; font-weight: 700; letter-spacing: 1px;
  }
  .brand-tagline {
    position: absolute; left: 0; right: 0; top: 364px;
    font-size: 19px; letter-spacing: 2px; text-transform: lowercase;
  }

  .flavour-band { position: relative; height: 354px; }
  .flavour-photo {
    position: absolute; left: 60px; right: 60px; top: 8px; height: 290px;
    background:
      radial-gradient(circle at 62% 58%, var(--lemon) 0%, transparent 28%),
      radial-gradient(circle at 38% 75%, var(--lime) 0%, transparent 24%),
      linear-gradient(180deg, #e9f1f3 0%, var(--paper) 40%);
  }
  .flavour-slogan {
    position: absolute; left: 0; right: 0; top: 318px;
    text-align: center; color: var(--ink-slogan);
    font-size: 17px; letter-spacing: 0.5px; text-transform: lowercase;
    white-space: nowrap;
  }
</style>
</head>
<body>
  <main class="label">
    <section class="mineral-band">
      <div class="mineral-texture" role="img" aria-label="Türkisfarbene Wasser- und Eisstruktur"></div>
      <ul class="element-list">
        <li class="element"><span class="element-symbol">Mg</span><span class="element-name">Magnesium</span></li>
        <li class="element"><span class="element-symbol">Na</span><span class="element-name">Natrium</span></li>
        <li class="element"><span class="element-symbol">Ca</span><span class="element-name">Kalzium</span></li>
        <li class="element"><span class="element-symbol">K</span><span class="element-name">Kalium</span></li>
      </ul>
    </section>

    <section class="brand-band">
      <div class="brand-mark" aria-hidden="true"></div>
      <h1 class="brand-name">FLUXO4</h1>
      <p class="brand-tagline">Elektrolyt-Getränk</p>
    </section>

    <section class="flavour-band">
      <div class="flavour-photo" role="img" aria-label="Zitrone und Limette fallen spritzend ins Wasser"></div>
      <p class="flavour-slogan">Dein Wachmacher in Zitrone-Limette Geschmack</p>
    </section>
  </main>
</body>
</html>
```